Business Card Design Project

This is the first time we use our new logo. We need a business card that we can use both on our institutional corporate relationships and also that works for our staff that deals with consumers directly.

VELUNDA is a new company dedicated to empower consumers and to provide them with the best choices for specialized health care using the latest telemedicine technology (medicine at a distance via videoconference).

We want to print this cards in high quality materials and process. We will like designs that allow us to use UV spot varnish and other techniques that will differentiate us.

We are including Two different versions of Color logos. In addition we are including white over black background logos. Those can be used replacing the black for a color.

Please note this is the first time we will be creating any corporate materials with our new logo and colors.

Target Market(s)

34+ consumers of medium high and high socioeconomic levels.

Industry/Entity Type

Health

Requirements
Must have
• Our logo on its original colors
Should not have
• Any other graphical element or design that is not our logo

```html
<!DOCTYPE html>
<html lang="en">
<head>
<meta charset="utf-8">
<title>Velunda business card</title>
<link rel="stylesheet" href="https://fonts.googleapis.com/css2?family=Montserrat:wght@600;700&family=Arimo:wght@400;700&display=swap">
<style>
  :root {
    --page: #e9e6e1;
    --card-white: #ffffff;
    --navy: #1b5a82;
    --blue: #2a74b8;
    --sky: #5fb4e0;
    --teal: #00a89c;
    --ink: #222831;
    --shadow: 0 14px 30px rgba(0,0,0,.22);
  }
  * { box-sizing: border-box; margin: 0; padding: 0; }
  html, body { width: 1200px; height: 1057px; overflow: hidden; background: var(--page); }
  .card {
    position: absolute; width: 620px; height: 354px;
    box-shadow: var(--shadow); overflow: hidden;
  }
  .card-front { left: 90px; top: 110px; background: var(--card-white); }
  .card-back { left: 490px; top: 590px; background: var(--teal); }
  .swoosh { position: absolute; inset: 0; width: 100%; height: 100%; }

  .brand {
    position: absolute; left: 56px; top: 62px;
    display: flex; align-items: center; gap: 16px;
  }
  .brand-dot { width: 42px; height: 42px; border-radius: 50%; background: var(--teal); }
  .brand-name {
    font-family: "Montserrat", sans-serif; font-weight: 700;
    font-size: 50px; letter-spacing: 6px; color: var(--navy);
  }

  .contact { position: absolute; left: 56px; top: 150px; font-family: "Arimo", sans-serif; }
  .person { font-family: "Montserrat", sans-serif; font-weight: 700; font-size: 22px; color: var(--navy); margin-bottom: 8px; }
  .person .title { font-family: "Arimo", sans-serif; font-weight: 400; font-size: 17px; color: var(--teal); }
  .contact-line { display: flex; align-items: center; gap: 8px; font-size: 17px; color: var(--ink); line-height: 25px; }
  .contact-line svg { width: 14px; height: 14px; flex: none; }

  .address {
    position: absolute; right: 26px; bottom: 26px; text-align: right;
    font-family: "Arimo", sans-serif; font-size: 15px; line-height: 20px; color: #fff;
  }

  .back-brand {
    position: absolute; left: 0; right: 0; top: 120px;
    display: flex; justify-content: center; align-items: center; gap: 18px;
  }
  .back-brand .brand-dot { width: 56px; height: 56px; background: #fff; }
  .back-brand .brand-name { color: #fff; font-size: 58px; }
  .back-web {
    position: absolute; left: 0; right: 0; bottom: 56px; text-align: center;
    font-family: "Arimo", sans-serif; font-weight: 700; font-size: 22px;
    letter-spacing: 6px; color: #fff;
  }
</style>
</head>
<body>
  <section class="card card-front">
    <svg class="swoosh" viewBox="0 0 620 354" aria-hidden="true">
      <path d="M360 354 C470 290 540 190 620 112 L620 354 Z" fill="var(--navy)"/>
      <path d="M330 354 C450 300 530 190 612 96" fill="none" stroke="var(--sky)" stroke-width="5"/>
      <path d="M350 354 C465 296 540 192 620 100" fill="none" stroke="var(--blue)" stroke-width="4"/>
      <path d="M0 300 C120 286 230 300 320 354 L0 354 Z" fill="var(--blue)"/>
      <path d="M0 318 C130 306 230 318 300 354 L0 354 Z" fill="var(--sky)"/>
      <path d="M0 334 C120 326 200 336 260 354 L0 354 Z" fill="var(--card-white)"/>
    </svg>

    <div class="brand">
      <span class="brand-dot"></span>
      <span class="brand-name">VELUNDA</span>
    </div>

    <div class="contact">
      <p class="person">Your Name, <span class="title">Title</span></p>
      <p class="contact-line">
        <svg viewBox="0 0 14 14"><circle cx="7" cy="7" r="6.5" fill="var(--navy)"/><path d="M5 4 L6.5 4 L7 6 L6 6.8 Q7 8.5 8 9 L8.8 8 L10.5 8.5 L10.5 10 Q7 10.5 4.5 6 Z" fill="#fff"/></svg>
        012-555-0142
      </p>
      <p class="contact-line">
        <svg viewBox="0 0 14 14"><circle cx="7" cy="7" r="6.5" fill="var(--navy)"/><path d="M5 4 L6.5 4 L7 6 L6 6.8 Q7 8.5 8 9 L8.8 8 L10.5 8.5 L10.5 10 Q7 10.5 4.5 6 Z" fill="#fff"/></svg>
        012-555-0142
      </p>
      <p class="contact-line">
        <svg viewBox="0 0 14 14"><rect x="1" y="3" width="12" height="8" rx="1" fill="var(--navy)"/><path d="M1.5 3.5 L7 8 L12.5 3.5" fill="none" stroke="#fff" stroke-width="1"/></svg>
        name@velunda.com
      </p>
      <p class="contact-line">
        <svg viewBox="0 0 14 14"><circle cx="7" cy="7" r="6" fill="var(--navy)"/><ellipse cx="7" cy="7" rx="2.5" ry="6" fill="none" stroke="#fff" stroke-width=".8"/><path d="M1 7 H13" stroke="#fff" stroke-width=".8"/></svg>
        www.velunda.com
      </p>
    </div>

    <p class="address">Street Name, City Name<br>State, City Zip Code</p>
  </section>

  <section class="card card-back">
    <div class="back-brand">
      <span class="brand-dot"></span>
      <span class="brand-name">VELUNDA</span>
    </div>
    <p class="back-web">www.velunda.com</p>
  </section>
</body>
</html>
```